Every Shelf Set Neatly or ESN Organized needs a business card design. ESN Organized is a professi

We need a business card design that is clean, sharp and conveys a sense of organization. I already have a logo.

Target Market(s)

Families (specifically mothers), small business owners, parents, seniors

Industry/Entity Type

Business

Contact Information for Business Card

My website is www.esnorganized-example.com and my Facebook page is http://www.sociallink-example.com/everyshelfsetneatly. The phone number is 418-552-7094 and I want to be listed as Lorna M. Pelham, Owner

Requirements
Must have
• My logo.

```html
<!DOCTYPE html>
<html lang="en">
<head>
<meta charset="utf-8">
<title>ESN Organized – Business Card</title>
<link rel="stylesheet" href="https://fonts.googleapis.com/css2?family=Open+Sans:wght@400;700&family=Montserrat:wght@300;400&display=swap">
<style>
  :root {
    --page-bg: #ececec;
    --card-white: #ffffff;
    --card-dark: #2a2a2a;
    --brand-blue: #1a7fd6;
    --ink-black: #111111;
    --text-dark: #222222;
    --logo-light: #ffffff;
  }
  * { box-sizing: border-box; margin: 0; padding: 0; }
  html, body {
    width: 1200px; height: 900px; overflow: hidden;
    background: var(--page-bg);
  }
  .canvas {
    position: relative; width: 1200px; height: 900px;
  }
  .card {
    position: absolute; left: 300px;
    width: 600px; height: 343px;
    box-shadow: 0 6px 18px rgba(0,0,0,0.18);
    overflow: hidden;
  }
  /* Back of card */
  .card-back {
    top: 70px;
    background: var(--card-dark);
    display: flex; align-items: center; justify-content: center;
  }
  .back-wordmark {
    font-family: "Montserrat", sans-serif;
    font-weight: 300;
    font-size: 64px;
    letter-spacing: 6px;
    color: var(--logo-light);
  }
  /* Front of card */
  .card-front {
    top: 480px;
    background: var(--card-white);
  }
  .front-shapes {
    position: absolute; inset: 0;
  }
  .owner {
    position: absolute; left: 62px; top: 20px;
    font-family: "Open Sans", sans-serif;
  }
  .owner-name {
    font-weight: 700; font-size: 17px; color: var(--brand-blue);
    line-height: 1.2;
  }
  .owner-title {
    font-size: 12px; color: var(--text-dark);
  }
  .contact-list {
    position: absolute; left: 30px; top: 150px;
    list-style: none;
    font-family: "Open Sans", sans-serif;
    font-size: 15px; color: var(--ink-black);
    line-height: 22px;
  }
  .contact-list li { display: flex; align-items: center; gap: 8px; }
  .contact-icon { width: 12px; height: 12px; flex: none; }
  .social-link {
    position: absolute; left: 20px; top: 262px;
    font-family: "Open Sans", sans-serif;
    font-size: 15px; color: var(--brand-blue);
  }
  .front-wordmark {
    position: absolute; left: 320px; top: 130px; width: 260px;
    text-align: center;
    font-family: "Montserrat", sans-serif;
    font-weight: 300;
    font-size: 30px;
    letter-spacing: 3px;
    line-height: 1.25;
    color: var(--brand-blue);
  }
</style>
</head>
<body>
<main class="canvas">

  <section class="card card-back" aria-label="Card back">
    <span class="back-wordmark">ESN Organized</span>
  </section>

  <section class="card card-front" aria-label="Card front">
    <svg class="front-shapes" width="600" height="343" viewBox="0 0 600 343" aria-hidden="true">
      <polygon points="0,18 40,18 28,34 0,34" fill="var(--brand-blue)"/>
      <polygon points="14,46 40,18 50,18 50,46" fill="var(--ink-black)"/>
      <polygon points="0,234 300,234 284,254 0,254" fill="var(--brand-blue)"/>
      <polygon points="312,296 600,296 600,343 278,343" fill="var(--ink-black)"/>
    </svg>

    <div class="owner">
      <p class="owner-name">Lorna M. Pelham</p>
      <p class="owner-title">Owner</p>
    </div>

    <ul class="contact-list">
      <li>
        <svg class="contact-icon" viewBox="0 0 12 12" aria-hidden="true"><path d="M2.5 1 L4.5 1 L5.2 3.6 L4 4.6 Q5 6.9 7.4 8 L8.4 6.8 L11 7.5 L11 9.5 Q10.5 11 9 11 Q1 10 1 3 Q1 1.5 2.5 1Z" fill="var(--brand-blue)"/></svg>
        418-552-7094
      </li>
      <li>
        <svg class="contact-icon" viewBox="0 0 12 12" aria-hidden="true"><rect x="0.5" y="2.5" width="11" height="7.5" fill="var(--brand-blue)"/><path d="M0.5 2.5 L6 7 L11.5 2.5" stroke="#fff" stroke-width="1" fill="none"/></svg>
        info@esnorganized-example.com
      </li>
      <li>
        <svg class="contact-icon" viewBox="0 0 12 12" aria-hidden="true"><circle cx="6" cy="6" r="5.5" fill="var(--brand-blue)"/><path d="M0.5 6 H11.5 M6 0.5 Q3 6 6 11.5 M6 0.5 Q9 6 6 11.5" stroke="#fff" stroke-width="0.8" fill="none"/></svg>
        www.esnorganized-example.com
      </li>
    </ul>

    <p class="social-link">www.sociallink-example.com/everyshelfsetneatly</p>

    <p class="front-wordmark">ESN Organized</p>
  </section>

</main>
</body>
</html>
```